Suds Haven Laundromat Wordpress Design

We need a Wordpress website design for our laundromat, Suds Haven Atlanta, at www.sudshavenatlanta-example.com. We would like to have 6 pages: Home, About Us, Services, Locations, Reviews and Contact us. We will provide content for the text on each page. What we do: We are a full service laundromat that provides dry cleaning drop off, professional laundry services, wash dry fold and self service laundry to the local community. We would like to use the color scheme from our logo to convey a warm, safe, and bright business that caters to its diverse community.
Updates

I like the structure of this laundromat website: http://www.washtroveusa-example.com/ Using my logo and color scheme in the above referenced website is what. Am looking for. The photos attached to the project with the female model should be used as a primary focus and supplemented by actual photos of the equipment.

Target Market(s)

Our target market is a diverse group of people from Midtown Atlanta - LGBTQ community /Locals/Regulars that have been coming to laundromat for 30 years.

Industry/Entity Type

Laundromat

Coding

Coded - Design and coding required

Number of Pages Required

5+ page

Font styles to use
Sans Serif

Colors
0054AA
0677BA
7BADD7
CADEEF
E8F1F8

Requirements
Must have
• Feature this video on the main page: https://videohost-example.com/xq7Rm2bPz4k

```html
<!DOCTYPE html>
<html lang="en">
<head>
<meta charset="utf-8">
<title>Suds Haven Laundromat</title>
<link href="https://fonts.googleapis.com/css2?family=Poppins:wght@500;600;700&family=Lato:wght@400;700&display=swap" rel="stylesheet">
<style>
:root{
  --navy:#0054AA;
  --blue:#0677BA;
  --sky:#1AA3DF;
  --soft:#7BADD7;
  --pale:#CADEEF;
  --mist:#E8F1F8;
  --ink:#141414;
  --grey:#6b6b6b;
  --white:#ffffff;
}
*{box-sizing:border-box;margin:0;padding:0}
html,body{width:1200px;height:3710px;overflow:hidden;background:var(--white)}
body{position:relative;font-family:'Lato',sans-serif;color:var(--ink)}
.abs{position:absolute}
h1,h2,h3,.nav,.btn,.brand{font-family:'Poppins',sans-serif}

/* header */
.site-header{position:absolute;left:0;top:0;width:1200px;height:89px;background:var(--white)}
.nav a{position:absolute;top:33px;font-size:15px;color:var(--ink);text-decoration:none;font-family:'Lato',sans-serif}
.brand{position:absolute;display:flex;align-items:center;gap:8px;color:var(--navy);font-weight:600}
.brand-dot{width:14px;height:14px;border-radius:50%;background:var(--sky)}
.btn{position:absolute;display:flex;align-items:center;justify-content:center;font-weight:600;font-size:14px;border-radius:4px 18px 4px 18px;text-decoration:none}
.btn-cyan{background:var(--sky);color:var(--white)}
.btn-white{background:var(--white);color:var(--sky)}

/* hero */
.hero-text{left:112px;color:var(--white)}
.hero-sub{font-family:'Poppins',sans-serif;font-weight:500;font-size:34px;top:270px}
.hero-title{font-weight:700;font-size:50px;top:312px;letter-spacing:.5px}
.hero-lede{top:378px;font-size:15px;line-height:26px}
.bubble{position:absolute;border:3px solid var(--white);border-radius:50%}

/* section titles */
.section-title{position:absolute;width:1200px;left:0;text-align:center;font-weight:700;font-size:30px;color:var(--ink)}
.section-title span{color:var(--navy)}
.section-title.light,.section-title.light span{color:var(--white)}

/* services */
.service-card{position:absolute;top:922px;width:249px;height:452px;border-radius:125px;background:linear-gradient(180deg,var(--sky) 0%,var(--navy) 100%);color:var(--white);text-align:center}
.service-photo{position:absolute;left:34px;top:32px;width:181px;height:181px;border-radius:50%;border:4px solid var(--white)}
.service-card h3{position:absolute;top:238px;width:100%;font-weight:500;font-size:19px}
.service-card p{position:absolute;top:282px;width:100%;font-size:15px;line-height:26px}
.plus{position:absolute;left:104px;top:384px;width:40px;height:40px;border-radius:50%;background:var(--white)}

/* about */
.about-copy{left:600px;top:1645px;width:460px;color:var(--white);font-size:15px;line-height:26px}

/* reviews */
.review-card{position:absolute;top:2283px;width:312px;height:258px;border-radius:22px;background:var(--white);box-shadow:0 2px 10px rgba(0,0,0,.14);text-align:center;color:var(--grey)}
.review-card.active{background:var(--sky);color:var(--white)}
.review-card p{position:absolute;top:55px;left:30px;right:30px;font-size:15px;line-height:26px}
.reviewer{position:absolute;top:185px;left:74px;display:flex;gap:12px;align-items:center;text-align:left}
.avatar{width:44px;height:44px;border-radius:50%;background:linear-gradient(135deg,var(--pale),var(--soft));border:2px solid var(--pale)}
.reviewer b{display:block;font-family:'Poppins',sans-serif;font-weight:500;font-size:16px;line-height:20px}
.reviewer small{font-size:12px;color:var(--blue)}
.review-card.active .reviewer small{color:var(--white)}
.review-card:not(.active) .reviewer b{color:var(--grey)}
.quote{position:absolute;top:2265px}
.arrow{position:absolute;top:2396px;width:34px;height:34px;border-radius:50%;border:2px solid var(--navy)}

/* contact */
.field{position:absolute;background:var(--white);border-radius:4px 22px 4px 22px;color:#888;font-size:15px;padding:18px 16px}
.submit{position:absolute;left:520px;top:3120px;width:160px;height:28px;color:var(--white);font-family:'Poppins',sans-serif;font-weight:600;font-size:14px;text-align:center}

/* footer */
.footer-head{position:absolute;top:3318px;font-family:'Poppins',sans-serif;font-weight:500;font-size:17px;color:var(--ink)}
.footer-list{position:absolute;top:3360px;font-size:15px;line-height:26px;color:var(--grey);list-style:none}
.footer-about{left:110px;top:3432px;width:260px;font-size:15px;line-height:26px;color:var(--grey)}
.divider{position:absolute;left:110px;top:3607px;width:978px;height:1px;background:var(--navy)}
.copyright{position:absolute;left:110px;top:3641px;font-size:15px;color:var(--grey)}
.social{position:absolute;top:3630px;width:40px;height:40px;border-radius:50%;background:#767676}
</style>
</head>
<body>

<header class="site-header">
  <nav class="nav">
    <a style="left:110px">Home</a>
    <a style="left:192px">About Us</a>
    <a style="left:295px">Services</a>
    <a style="left:393px">Locations</a>
    <a style="left:762px">Reviews</a>
    <a style="left:859px">Contact us</a>
  </nav>
  <div class="brand" style="left:514px;top:28px;font-size:22px"><span class="brand-dot"></span>Suds Haven</div>
  <a class="btn btn-cyan" style="left:968px;top:21px;width:120px;height:44px">LOG IN</a>
</header>

<!-- hero -->
<svg class="abs" style="left:0;top:89px" width="1200" height="670" viewBox="0 0 1200 670">
  <defs>
    <linearGradient id="heroFill" x1="0" y1="0" x2="0" y2="1">
      <stop offset="0" stop-color="#0a62c4"/><stop offset="1" stop-color="#0858b3"/>
    </linearGradient>
  </defs>
  <path d="M0 0H1200V500C1120 470 1060 540 980 580C880 640 770 670 670 640C540 600 420 540 280 520C150 500 60 520 0 540Z" fill="var(--sky)"/>
  <path d="M0 0H1200V500C1110 490 1060 560 960 600C860 640 770 640 660 610C540 575 430 520 290 512C160 505 60 520 0 530Z" fill="url(#heroFill)"/>
</svg>
<div class="bubble" style="left:179px;top:160px;width:14px;height:14px"></div>
<div class="bubble" style="left:220px;top:178px;width:26px;height:26px"></div>
<div class="bubble" style="left:181px;top:202px;width:11px;height:11px"></div>
<div class="bubble" style="left:258px;top:217px;width:14px;height:14px"></div>
<div class="bubble" style="left:317px;top:121px;width:14px;height:14px"></div>
<div class="abs hero-text hero-sub">WELCOME TO</div>
<h1 class="abs hero-text hero-title">SUDS HAVEN</h1>
<p class="abs hero-text hero-lede">A full service laundromat, consectetur adipiscing elit,<br>sed do eiusmod tempor incididunt</p>
<a class="btn btn-cyan" style="left:112px;top:446px;width:137px;height:44px">GET STARTED</a>
<svg class="abs" style="left:640px;top:390px" width="50" height="50" viewBox="0 0 50 50" aria-label="Play video">
  <circle cx="25" cy="25" r="25" fill="var(--white)"/><path d="M20 15L35 25L20 35Z" fill="var(--navy)"/>
</svg>
<div class="abs" style="left:734px;top:132px;width:396px;height:412px;border-radius:50%;border-top:6px solid var(--sky);border-right:6px solid var(--sky)"></div>
<div class="abs" role="img" aria-label="Model in a blue dress standing by laundromat washers" style="left:740px;top:150px;width:380px;height:390px;border-radius:50%;background:linear-gradient(160deg,#8fa4b5,#3f7fcf 55%,#6c7d8a)"></div>

<!-- services -->
<h2 class="section-title" style="top:834px">OUR <span>SERVICES</span></h2>
<div class="service-card" style="left:163px">
  <div class="service-photo" role="img" aria-label="Front-load dry cleaning machines" style="background:linear-gradient(160deg,#e8ecee,#a6adb2)"></div>
  <h3>Dry cleaning drop off</h3>
  <p>Lorem ipsum dolor sit amet,<br>consectetur adipiscing elit,<br>sed do eiusmod tempor</p>
  <svg class="plus" viewBox="0 0 40 40"><path d="M20 13V27M13 20H27" stroke="var(--navy)" stroke-width="2"/></svg>
</div>
<div class="service-card" style="left:476px">
  <div class="service-photo" role="img" aria-label="Row of washers under a laundromat sign" style="background:linear-gradient(180deg,#c9d2d6,#6a7278)"></div>
  <h3>Professional laundry</h3>
  <p>Lorem ipsum dolor sit amet,<br>consectetur adipiscing elit,<br>sed do eiusmod tempor</p>
  <svg class="plus" viewBox="0 0 40 40"><path d="M20 13V27M13 20H27" stroke="var(--navy)" stroke-width="2"/></svg>
</div>
<div class="service-card" style="left:788px">
  <div class="service-photo" role="img" aria-label="Laundromat aisle with stacked dryers" style="background:linear-gradient(160deg,#dde2e4,#7e878c)"></div>
  <h3>Wash dry fold</h3>
  <p>Lorem ipsum dolor sit amet,<br>consectetur adipiscing elit,<br>sed do eiusmod tempor</p>
  <svg class="plus" viewBox="0 0 40 40"><path d="M20 13V27M13 20H27" stroke="var(--navy)" stroke-width="2"/></svg>
</div>

<!-- about -->
<svg class="abs" style="left:0;top:1455px" width="1200" height="620" viewBox="0 0 1200 620">
  <path d="M0 5C200 60 450 30 700 25C950 20 1100 10 1200 40V570C1000 540 800 560 600 590C400 615 200 600 0 560Z" fill="var(--soft)"/>
  <path d="M0 30C200 75 450 50 700 45C950 40 1100 35 1200 60V555C1000 530 800 550 600 580C400 605 200 590 0 550Z" fill="var(--sky)"/>
</svg>
<div class="bubble" style="left:106px;top:1531px;width:24px;height:24px"></div>
<div class="bubble" style="left:174px;top:1570px;width:14px;height:14px"></div>
<div class="bubble" style="left:37px;top:1609px;width:14px;height:14px"></div>
<div class="bubble" style="left:79px;top:1625px;width:26px;height:26px"></div>
<div class="bubble" style="left:39px;top:1650px;width:11px;height:11px"></div>
<div class="bubble" style="left:116px;top:1664px;width:14px;height:14px"></div>
<div class="abs" style="left:128px;top:1596px;width:380px;height:380px;border-radius:50%;border-left:8px solid var(--navy);border-top:8px solid var(--navy)"></div>
<div class="abs" role="img" aria-label="Model seated in front of a row of numbered washers" style="left:138px;top:1602px;width:372px;height:372px;border-radius:50%;background:linear-gradient(180deg,#b9d8d4 0%,#cfd4d0 35%,#556068 70%,#a9b0b4 100%)"></div>
<h2 class="abs" style="left:600px;top:1585px;font-weight:600;font-size:28px;color:var(--white)">ABOUT SUDS HAVEN</h2>
<p class="abs about-copy">Lorem ipsum dolor sit amet, consectetur adipiscing elit, sed do eiusmod tempor incididunt ut labore et dolore magna aliqua. Ut enim ad minim veniam, quis nostrud exercitation ullamco laboris nisi ut aliquip ex ea commodo consequat. Duis aute irure dolor in reprehenderit in voluptate velit esse cillum dolore eu fugiat nulla pariatur. Excepteur sint occaecat cupidatat non proident, sunt in culpa qui officia deserunt mollit anim id est laborum.</p>
<a class="btn btn-white" style="left:600px;top:1858px;width:137px;height:44px">GET STARTED</a>

<!-- reviews -->
<h2 class="section-title" style="top:2167px">CLIENT <span>REVIEWS</span></h2>
<svg class="arrow" style="left:51px;border-color:var(--soft)" viewBox="0 0 34 34"><path d="M19 11L13 17L19 23" stroke="var(--soft)" stroke-width="2" fill="none"/></svg>
<svg class="arrow" style="left:1112px" viewBox="0 0 34 34"><path d="M15 11L21 17L15 23" stroke="var(--navy)" stroke-width="2" fill="none"/></svg>
<div class="review-card" style="left:110px">
  <p>Lorem ipsum dolor sit amet, consectetur adipiscing elit, sed do eiusmod tempor incididunt ut labore et dolore magna aliqua.</p>
  <div class="reviewer"><div class="avatar" role="img" aria-label="Reviewer portrait"></div><div><b>DANA REYES</b><small>Lorem ipsum dolor</small></div></div>
</div>
<div class="review-card active" style="left:442px">
  <p>Lorem ipsum dolor sit amet, consectetur adipiscing elit, sed do eiusmod tempor incididunt ut labore et dolore magna aliqua.</p>
  <div class="reviewer"><div class="avatar" role="img" aria-label="Reviewer portrait"></div><div><b>DANA REYES</b><small>Lorem ipsum dolor</small></div></div>
</div>
<div class="review-card" style="left:774px">
  <p>Lorem ipsum dolor sit amet, consectetur adipiscing elit, sed do eiusmod tempor incididunt ut labore et dolore magna aliqua.</p>
  <div class="reviewer"><div class="avatar" role="img" aria-label="Reviewer portrait"></div><div><b>DANA REYES</b><small>Lorem ipsum dolor</small></div></div>
</div>
<svg class="quote" style="left:128px" width="44" height="32" viewBox="0 0 44 32"><path d="M2 32V16Q2 4 14 2V8Q9 10 9 16H18V32ZM24 32V16Q24 4 36 2V8Q31 10 31 16H40V32Z" fill="var(--navy)"/></svg>
<svg class="quote" style="left:460px" width="44" height="32" viewBox="0 0 44 32"><path d="M2 32V16Q2 4 14 2V8Q9 10 9 16H18V32ZM24 32V16Q24 4 36 2V8Q31 10 31 16H40V32Z" fill="var(--navy)"/></svg>
<svg class="quote" style="left:792px" width="44" height="32" viewBox="0 0 44 32"><path d="M2 32V16Q2 4 14 2V8Q9 10 9 16H18V32ZM24 32V16Q24 4 36 2V8Q31 10 31 16H40V32Z" fill="var(--navy)"/></svg>

<!-- contact -->
<svg class="abs" style="left:0;top:2620px" width="1200" height="620" viewBox="0 0 1200 620">
  <path d="M0 5C150 45 350 55 600 40C850 25 1050 20 1200 30V565C1000 560 800 570 600 590C400 610 200 610 0 585Z" fill="var(--soft)"/>
  <path d="M0 30C150 70 350 75 600 60C850 45 1050 45 1200 55V550C1000 545 800 555 600 575C400 595 200 595 0 570Z" fill="#0a5ec2"/>
</svg>
<div class="bubble" style="left:1043px;top:2718px;width:26px;height:26px"></div>
<div class="bubble" style="left:1110px;top:2754px;width:14px;height:14px"></div>
<div class="bubble" style="left:973px;top:2790px;width:14px;height:14px"></div>
<div class="bubble" style="left:1016px;top:2812px;width:26px;height:26px"></div>
<div class="bubble" style="left:976px;top:2832px;width:11px;height:11px"></div>
<div class="bubble" style="left:1052px;top:2848px;width:14px;height:14px"></div>
<h2 class="section-title light" style="top:2750px">CONTACT <span>US</span></h2>
<div class="field" style="left:314px;top:2815px;width:278px;height:60px">Name</div>
<div class="field" style="left:608px;top:2815px;width:279px;height:60px">Phone</div>
<div class="field" style="left:314px;top:2893px;width:278px;height:59px">Email</div>
<div class="field" style="left:608px;top:2893px;width:279px;height:59px">Subject</div>
<div class="field" style="left:314px;top:2974px;width:573px;height:112px">Message</div>
<div class="submit">SUBMIT NOW</div>

<!-- footer -->
<div class="brand" style="left:110px;top:3355px;font-size:28px"><span class="brand-dot" style="width:18px;height:18px"></span>Suds Haven</div>
<p class="abs footer-about">Lorem ipsum dolor sit amet, consectetur adipiscing elit, sed do eiusmod tempor incididunt ut labore et dolore magna aliqua.</p>
<div class="footer-head" style="left:457px">QUICK LINKS</div>
<ul class="footer-list" style="left:457px"><li>Home</li><li>About Us</li><li>Services</li><li>Locations</li><li>Reviews</li><li>Contact us</li></ul>
<div class="footer-head" style="left:650px">OUR SERVICES</div>
<ul class="footer-list" style="left:650px"><li>Dry cleaning drop off</li><li>Professional laundry</li><li>Wash dry fold</li></ul>
<div class="footer-head" style="left:854px">EMAIL</div>
<div class="footer-list" style="left:854px">hello@sudshavenatlanta-example.com</div>
<div class="footer-head" style="left:854px;top:3403px">PHONE</div>
<div class="footer-list" style="left:854px;top:3444px">(555) 014-2298</div>
<div class="footer-head" style="left:854px;top:3486px">ADDRESS</div>
<div class="footer-list" style="left:854px;top:3527px">2210 Maple Row NE., # 118,<br>Atlanta, GA 30399</div>
<div class="divider"></div>
<div class="copyright">©Copyrights 2021 Company Name &nbsp;|&nbsp;&nbsp; All Rights Reserved</div>
<div class="social" style="left:874px"></div>
<div class="social" style="left:932px"></div>
<div class="social" style="left:989px"></div>
<div class="social" style="left:1046px"></div>

</body>
</html>
```